Car rental website design for a UAE car rental company

This project is about creating a new website design for a car rental company located in Dubai (United Arab Emirates), I opened the same project a few months ago but I didn't receive a lot of appealing entries so I closed it but this time I am marking the project as guaranteed to avoid such situation again, if you have already provided a design before then please re-submit again on this project so that it is considered while reviewing all the designs

A few important things:

1- We need a simple non-complex design
2- The final deliverable would be 2 screens (PSD, JPEG ... etc), the first screen is for the home page and the second screen is for an internal page
3- The home page must have a section that end users can use to rent a car online directly from the home page instead of going into some inner pages
4- The current website is very old and not very appealing so avoid creating a similar design (www.crestvane-autos.example)
5- The name is Crestvane but the company rents normal cars (no Limousin cars will be rented) so avoid adding any fancy cars in the images/graphics used in the design, just normal end users cars
6- The expected pages would be: home, About us, Our team, Strategy, Contact us and links to social media pages
7- The attachments include the company's logo and some screens from other car rental companies that provide online rentals/payments

If you have any questions please feel free to ask and please note that we will need the designs urgently

Thanks

Target Market(s)

Dubai - United Arab Emirates

Industry/Entity Type

It Company

Number of Pages Required

2 page

Font styles to use
Sans Serif

Requirements
Must have
• Check the project details
Nice to have
Should not have

```html
<!DOCTYPE html>
<html lang="en">
<head>
<meta charset="utf-8">
<title>Crestvane – Rent A Car</title>
<link href="https://fonts.googleapis.com/css2?family=Open+Sans:wght@400;600;700&display=swap" rel="stylesheet">
<style>
:root{
  --red:#c8161d;
  --dark:#232323;
  --panel:rgba(38,38,38,.9);
  --field:#f4f4f4;
  --muted:#8d8d8d;
  --white:#ffffff;
  --grey-btn:#5b5b5b;
}
*{box-sizing:border-box;margin:0;padding:0}
html,body{width:1200px;height:590px;overflow:hidden}
body{position:relative;font-family:"Open Sans",Arial,sans-serif;color:var(--white);background:var(--dark)}
.hero-photo{position:absolute;left:0;top:0;width:1200px;height:408px;
  background:linear-gradient(180deg,#7f93a6 0%,#9a8e7e 14%,#a5703f 30%,#8a5a30 48%,#5c4c3c 62%,#3a3a3a 78%,#2a2a2a 100%)}
.logo-box{position:absolute;left:293px;top:0;width:84px;height:96px;background:rgba(225,225,225,.85);
  display:flex;flex-direction:column;align-items:center;justify-content:center;gap:8px}
.logo-mark{width:22px;height:22px;background:var(--red)}
.logo-name{font-size:12px;font-weight:600;color:#5a5a5a}
.top-actions{position:absolute;top:10px;right:293px;display:flex;gap:14px}
.top-btn{height:18px;padding:0 7px;font-size:8.5px;line-height:18px;text-transform:uppercase;background:var(--grey-btn);border:1px solid #888;color:var(--white)}
.top-btn.primary{background:var(--red);border-color:var(--red)}
.main-nav{position:absolute;top:50px;right:293px;display:flex;gap:23px;font-size:11.5px;font-weight:600;text-transform:uppercase}
.headline{position:absolute;left:293px;top:174px;font-weight:700;font-size:17px;text-transform:uppercase}
.headline span{display:inline-block;padding:5px 9px}
.headline .line-one{background:rgba(30,30,30,.85)}
.headline .line-two{background:var(--red);margin-top:3px}
.slider-dots{position:absolute;left:293px;top:376px;display:flex;gap:4px}
.slider-dots i{width:7px;height:7px;background:var(--white)}
.slider-dots i.active{background:var(--red)}
.booking{position:absolute;left:718px;top:109px;width:189px;height:273px;background:var(--panel);border-radius:3px;overflow:hidden}
.booking-tabs{display:flex;height:31px;font-size:9px}
.booking-tabs .tab{display:flex;align-items:center;justify-content:center;text-align:center;line-height:1.1}
.booking-tabs .active{width:70px;background:var(--red);font-size:10px}
.booking-tabs .tab:last-child{flex:1;background:#3b3b3b}
.booking-form{padding:9px 9px 0}
.field{height:22px;background:var(--field);color:#a3a3a3;font-size:8.5px;padding:0 7px;display:flex;align-items:center;justify-content:space-between;margin-bottom:10px}
.field::after{content:"";border:3px solid transparent;border-top-color:#999;margin-top:3px}
.label-row{display:flex;justify-content:space-between;font-size:9px;margin:2px 0 6px;padding-right:32px}
.date-row{display:flex;gap:4px;margin-bottom:10px}
.date-row .field{margin:0;padding:0 3px;font-size:7.5px}
.date-row .dd,.date-row .mm{width:26px}
.date-row .yyyy{width:36px;margin-right:16px}
.date-row .time{width:49px}
.book-btn{display:block;margin:4px auto 0;width:84px;height:20px;background:var(--red);font-size:9px;line-height:20px;text-align:center;text-transform:uppercase}
.site-footer{position:absolute;left:0;top:408px;width:1200px;height:151px;background:var(--dark)}
.footer-col{position:absolute;top:30px}
.footer-col h3{font-size:11px;font-weight:600;text-transform:uppercase;margin-bottom:12px}
.gallery{left:293px}
.gallery-grid{display:grid;grid-template-columns:repeat(3,48px);gap:5px}
.gallery-grid div{height:38px;border:1px solid #777}
.thumb-a{background:linear-gradient(#8aa0b5,#a03030)}
.thumb-b{background:linear-gradient(#c98a4a,#4fae3a)}
.thumb-c{background:linear-gradient(#222,#d8d8d8)}
.links{left:502px}
.links li{list-style:none;font-size:9px;color:var(--muted);margin-bottom:8px}
.contact{left:637px;width:150px}
.contact-item{display:flex;gap:8px;font-size:8.5px;color:var(--muted);line-height:1.3;margin-bottom:9px}
.contact-item svg{flex:none;margin-top:1px}
.follow{left:829px}
.social-grid{display:grid;grid-template-columns:repeat(3,19px);gap:7px 8px}
.social-grid div{width:19px;height:19px;background:#b9b9b9;border-radius:2px}
.bottom-bar{position:absolute;left:0;top:559px;width:1200px;height:31px;background:var(--red)}
.copyright{position:absolute;left:293px;top:9px;font-size:10px}
.payments{position:absolute;right:293px;top:5px;display:flex;gap:7px}
.payments div{width:33px;height:21px;background:var(--white);border-radius:2px}
</style>
</head>
<body>
<div class="hero-photo" role="img" aria-label="Photo of a bright green coupe on an open road with blurred hills and fields behind"></div>

<div class="logo-box">
  <div class="logo-mark"></div>
  <div class="logo-name">Crestvane</div>
</div>

<div class="top-actions">
  <a class="top-btn primary">Rent a car</a>
  <a class="top-btn">Register</a>
  <a class="top-btn">Login now</a>
</div>

<nav class="main-nav">
  <a>Home</a><a>About us</a><a>Our team</a><a>Strategy</a><a>Contact us</a>
</nav>

<div class="headline">
  <span class="line-one">Book your favourate car for rent,</span><br>
  <span class="line-two">and enjoy your trip</span>
</div>

<div class="slider-dots"><i class="active"></i><i></i><i></i><i></i></div>

<section class="booking">
  <div class="booking-tabs">
    <div class="tab active">Book A Car</div>
    <div class="tab">View,Change or Cancel<br>Car Reservation</div>
  </div>
  <div class="booking-form">
    <div class="field">Pick up location</div>
    <div class="field">Return location</div>
    <div class="label-row"><span>Pick up date</span><span>Time</span></div>
    <div class="date-row">
      <div class="field dd">DD</div><div class="field mm">MM</div><div class="field yyyy">YYYY</div><div class="field time">12:00 PM</div>
    </div>
    <div class="label-row"><span>Return date</span><span>Time</span></div>
    <div class="date-row">
      <div class="field dd">DD</div><div class="field mm">MM</div><div class="field yyyy">YYYY</div><div class="field time">12:00 PM</div>
    </div>
    <div class="field">Vehicle Type</div>
    <a class="book-btn">Book car now</a>
  </div>
</section>

<footer class="site-footer">
  <div class="footer-col gallery">
    <h3>Car gallery</h3>
    <div class="gallery-grid" role="img" aria-label="Thumbnails of rental cars">
      <div class="thumb-a"></div><div class="thumb-b"></div><div class="thumb-c"></div>
      <div class="thumb-a"></div><div class="thumb-b"></div><div class="thumb-c"></div>
    </div>
  </div>
  <div class="footer-col links">
    <h3>Important links</h3>
    <ul><li>Home</li><li>About us</li><li>Our team</li><li>Strategy</li><li>Contact us</li></ul>
  </div>
  <div class="footer-col contact">
    <h3>Contact us</h3>
    <div class="contact-item">
      <svg width="10" height="12" viewBox="0 0 10 12"><path d="M5 0a4 4 0 0 0-4 4c0 3 4 8 4 8s4-5 4-8a4 4 0 0 0-4-4zm0 5.5A1.5 1.5 0 1 1 5 2.5a1.5 1.5 0 0 1 0 3z" fill="#8d8d8d"/></svg>
      <span>220 Harbor Crest Avenue,<br>Deira, Dubai 00000 near the<br>Creekside Plaza</span>
    </div>
    <div class="contact-item">
      <svg width="10" height="11" viewBox="0 0 10 11"><path d="M2 0l2 2.5-1.2 1.3c.6 1.5 1.8 2.7 3.3 3.3L7.5 6 10 8 8.5 10.5C4 10 0 6 0 1.5z" fill="#8d8d8d"/></svg>
      <span>1-800-555-RIDE<br>or 1-800-555-0142</span>
    </div>
    <div class="contact-item">
      <svg width="11" height="11" viewBox="0 0 11 11"><circle cx="5.5" cy="5.5" r="4.8" fill="none" stroke="#8d8d8d"/><path d="M.7 5.5h9.6M5.5.7c-2 2.6-2 7 0 9.6M5.5.7c2 2.6 2 7 0 9.6" fill="none" stroke="#8d8d8d" stroke-width=".8"/></svg>
      <span>www.crestvane-autos.example</span>
    </div>
  </div>
  <div class="footer-col follow">
    <h3>Follow us on</h3>
    <div class="social-grid"><div></div><div></div><div></div><div></div><div></div><div></div></div>
  </div>
</footer>

<div class="bottom-bar">
  <p class="copyright">All Rights Reserved @ www.crestvane-autos.example</p>
  <div class="payments"><div></div><div></div><div></div><div></div></div>
</div>
</body>
</html>
```